International Medical Company Needs a Website Design for a Support Site

We need a website design for a support site we are doing for ostomates called Bright Returns. We are an international company but this website is for our Australian market.

The website is a support site for people who are living with an Ostomy or Bowel Disease. This is a site where they can read other ostomates' stories and how they are dealing with the fact that they have to wear a pouch everyday.

The URL for our US site is: http://www.brightreturnsite.example/

We need to use the same logo but we have freedom around the color scheme. We are not fond of the brown color scheme used in our US site and are happy for designs to be submitted with alternatives.

• We want the design to be clean, inspiring, modern and inviting.
• We would like to see a design for the mainpage / homepage and one of the subpages
• We only require the PSD / image files (no HTML needed)

Attached to this project is our sitemap, an example wireframe and the logos. We are happy for you to play around with different options and don't have to stick to the layout shown in the wireframe.

If you have any further questions please ask.

Industry/Entity Type

It Company

```html
<!DOCTYPE html>
<html lang="en">
<head>
<meta charset="utf-8">
<title>Bright Returns – Sharing Stories and Giving Hope</title>
<link href="https://fonts.googleapis.com/css2?family=Bitter:wght@400;500&family=Open+Sans:wght@400;600&display=swap" rel="stylesheet">
<style>
  :root {
    --orange: #fba43a;
    --heading: #c7771d;
    --ink: #1e1e1e;
    --black: #000;
    --panel: #e9eaeb;
    --border: #b9b9b9;
    --icon: #3a3a3a;
    --white: #fff;
    --sky-deep: #1f55c9;
    --sky-light: #dbe6f4;
  }
  * { box-sizing: border-box; margin: 0; padding: 0; }
  html, body { width: 1200px; height: 695px; overflow: hidden; background: var(--white); }
  body { position: relative; font-family: "Open Sans", Arial, sans-serif; color: var(--ink); }
  .abs { position: absolute; }

  .brand { left: 152px; top: 62px; width: 160px; display: flex; align-items: center; gap: 7px;
    font-family: "Open Sans", Arial, sans-serif; font-weight: 600; font-size: 14px; letter-spacing: .5px; color: var(--heading); }
  .brand-dot { width: 14px; height: 14px; border-radius: 50%; background: var(--orange); flex: none; }

  .btn { display: flex; align-items: center; justify-content: center; background: var(--orange);
    color: var(--ink); font-size: 13.5px; text-decoration: none; }
  .btn-top { left: 776px; top: 15px; width: 122px; height: 31px; }
  .country { left: 912px; top: 19px; width: 136px; height: 25px; border: 1px solid #999; border-radius: 2px;
    font-size: 10.5px; padding: 5px 8px; display: flex; justify-content: space-between; align-items: center; }
  .country svg { width: 9px; height: 6px; }

  .nav { left: 330px; top: 69px; width: 718px; height: 34px; background: var(--black); display: flex; align-items: center; }
  .nav a { color: var(--white); text-decoration: none; font-size: 13.5px; padding: 0 12px; height: 34px;
    display: flex; align-items: center; border-right: 1px solid #555; }
  .nav a:first-child { padding-left: 15px; }
  .nav a:last-of-type { border-right: none; }
  .search { position: absolute; left: 549px; top: 5px; width: 163px; height: 23px; border: 1px solid #666;
    background: #222; color: #bbb; font-size: 11px; padding: 4px 9px; display: flex; justify-content: space-between; align-items: center; }
  .search svg { width: 13px; height: 13px; }

  .hero-panel { left: 152px; top: 113px; width: 353px; height: 299px; background: var(--panel); }
  .hero-title { left: 182px; top: 150px; font-family: "Bitter", Georgia, serif; font-weight: 400;
    font-size: 25px; line-height: 31px; color: var(--heading); }
  .hero-text { left: 183px; top: 221px; width: 310px; font-size: 13.5px; line-height: 23px; }
  .btn-hero-share { left: 186px; top: 318px; width: 121px; height: 33px; }
  .hero-or { left: 327px; top: 325px; font-size: 13.5px; }
  .btn-hero-read { left: 370px; top: 318px; width: 122px; height: 33px; }
  .hero-photo { left: 505px; top: 113px; width: 543px; height: 299px;
    background: linear-gradient(200deg, var(--sky-deep) 0%, #4d80da 45%, var(--sky-light) 80%, #fff 100%); }

  .card { top: 422px; width: 290px; height: 219px; border: 1px solid var(--border);
    background: linear-gradient(var(--white) 60%, #f6f6f6); }
  .card-about { left: 152px; }
  .card-share { left: 456px; }
  .card-news { left: 758px; }
  .card-icon { position: absolute; left: 14px; top: 14px; width: 34px; height: 34px; }
  .card-title { position: absolute; left: 64px; top: 14px; width: 200px; font-family: "Bitter", Georgia, serif;
    font-size: 19.5px; line-height: 22px; color: var(--heading); }
  .card-share .card-title, .card-news .card-title { top: 20px; }
  .card-body { position: absolute; left: 64px; top: 68px; width: 220px; font-size: 12.5px; line-height: 22px; }
  .news-arrows { position: absolute; right: 14px; top: 16px; width: 28px; height: 14px; }
  .news-list { position: absolute; left: 65px; top: 54px; width: 200px; }
  .news-item h3 { font-size: 12.5px; font-weight: 600; line-height: 16px; }
  .news-item p { font-size: 11px; line-height: 16.5px; }
  .news-item a { font-size: 11px; font-weight: 600; color: var(--ink); text-decoration: none; }
  .news-item + .news-item { border-top: 1px dotted #555; margin-top: 6px; padding-top: 10px; }

  .footer { left: 152px; top: 651px; width: 896px; height: 37px; background: var(--black); color: #ddd;
    font-size: 11px; display: flex; justify-content: space-between; align-items: center; padding: 0 14px; }
  .footer nav a { color: #ddd; text-decoration: none; }
</style>
</head>
<body>
  <div class="abs brand"><span class="brand-dot"></span>BRIGHT RETURNS</div>

  <a class="abs btn btn-top" href="#">Share a Story</a>
  <div class="abs country">United States
    <svg viewBox="0 0 9 6"><path d="M0 0h9L4.5 6z" fill="#222"/></svg>
  </div>

  <nav class="abs nav">
    <a href="#">About Us</a>
    <a href="#">Persoal Stories</a>
    <a href="#">Tips for Living</a>
    <a href="#">News</a>
    <a href="#">Resources</a>
    <a href="#">Contact Us</a>
    <div class="search">Search
      <svg viewBox="0 0 13 13"><circle cx="5" cy="5" r="3.8" fill="none" stroke="#ccc" stroke-width="1.6"/><path d="M8 8l4 4" stroke="#ccc" stroke-width="2"/></svg>
    </div>
  </nav>

  <section>
    <div class="abs hero-panel"></div>
    <h1 class="abs hero-title">Sharing Stories and<br>Giving Hope</h1>
    <p class="abs hero-text">to people around the world who are facing inflammatory bowel disease, colorectal cancer, or have had ostomy surgery.</p>
    <a class="abs btn btn-hero-share" href="#">Share a Story</a>
    <span class="abs hero-or">OR</span>
    <a class="abs btn btn-hero-read" href="#">Read Stories</a>
    <div class="abs hero-photo" role="img" aria-label="Photo of a young climber scaling a rock against a bright blue sky with clouds"></div>
  </section>

  <article class="abs card card-about">
    <svg class="card-icon" viewBox="0 0 34 34"><circle cx="17" cy="17" r="17" fill="var(--icon)"/><text x="17" y="25" text-anchor="middle" font-family="Open Sans, sans-serif" font-weight="600" font-size="22" fill="var(--orange)">?</text></svg>
    <h2 class="card-title">What is Bright Returns</h2>
    <p class="card-body">Congratulations to Daniel Hartwell of Millbrook, MD, named this year’s Bright Returns® National Award recipient at at the Wound and Continence Care Nurses (WCCN) Society 45th Annual ...</p>
  </article>

  <article class="abs card card-share">
    <svg class="card-icon" viewBox="0 0 34 34"><circle cx="17" cy="17" r="17" fill="var(--icon)"/><g fill="var(--orange)" stroke="var(--orange)" stroke-width="2"><path d="M13 17l9-5M13 17l9 5"/><circle cx="12" cy="17" r="3"/><circle cx="22" cy="11.5" r="3"/><circle cx="22" cy="22.5" r="3"/></g></svg>
    <h2 class="card-title">Share a Story</h2>
    <p class="card-body">Congratulations to Daniel Hartwell of Millbrook, MD, named this year’s Bright Returns® National Award recipient at at the Wound and Continence Care Nurses (WCCN) Society 45th Annual ...</p>
  </article>

  <article class="abs card card-news">
    <svg class="card-icon" viewBox="0 0 34 34"><circle cx="17" cy="17" r="17" fill="var(--icon)"/><g fill="var(--orange)" stroke="var(--orange)" stroke-width="2"><path d="M13 17l9-5M13 17l9 5"/><circle cx="12" cy="17" r="3"/><circle cx="22" cy="11.5" r="3"/><circle cx="22" cy="22.5" r="3"/></g></svg>
    <h2 class="card-title">News</h2>
    <svg class="news-arrows" viewBox="0 0 28 14"><path d="M6 1L1 7l5 6M22 1l5 6-5 6" fill="none" stroke="#222" stroke-width="1.4"/></svg>
    <div class="news-list">
      <div class="news-item">
        <h3>A Message from Martin Ashdown</h3>
        <p>It is hard to believe that Bright Returns is almost 30 years old now but it is!</p>
        <a href="#">Read More &gt;&gt;</a>
      </div>
      <div class="news-item">
        <h3>Make Your Voice Heard on World Ostomy Day!</h3>
        <p>To recognize World Ostomy Day on October 6, Corvanta, the sponsor of</p>
      </div>
    </div>
  </article>

  <footer class="abs footer">
    <span>Copyrights @ 2014 All Rights Reserved</span>
    <nav><a href="#">Legal Notice</a> &nbsp;|&nbsp; <a href="#">Privacy Policy</a> &nbsp;|&nbsp; <a href="#">Sitemap</a></nav>
  </footer>
</body>
</html>
```